Harborline Renewal Business Card Design

Professional and clean design. The design colors should flow with the logo. Two-sided card with the website on the back which is:

www.HarborlineRenewal.example.

"Specializing in Water Damage Restoration"

On the front I need the name, email, phone, and logo.

Name: Darnell Quisby
Email: Darnell@HarborlineRenewal.example
Phone: 555-318-2046 for now

I only have the Preview and Thumbnail right now but should have the source files uploaded within a day or two.

Target Market(s)

Flood victims, home owners with water damage from busted pipes etc...

Industry/Entity Type

Business

Contact Information for Business Card

Name: Darnell Quisby

Font styles to use
Serif
Sans Serif

Requirements
Must have
• Business Card Details Info

```html
<!DOCTYPE html>
<html lang="en">
<head>
<meta charset="utf-8">
<title>Harborline Renewal – Business Card</title>
<link rel="stylesheet" href="https://fonts.googleapis.com/css2?family=Cinzel:wght@600&family=Open+Sans:wght@400;700&display=swap">
<style>
  :root {
    --brand-blue: #2597d6;
    --brand-blue-light: #4fb8ec;
    --card-white: #ffffff;
    --backdrop: #2a2a2c;
  }
  * { box-sizing: border-box; margin: 0; padding: 0; }
  html, body { width: 1200px; height: 900px; overflow: hidden; }
  body {
    background: var(--backdrop);
    font-family: "Open Sans", Arial, sans-serif;
    position: relative;
  }
  .card {
    position: absolute;
    width: 520px;
    height: 300px;
    border-radius: 26px;
    overflow: hidden;
  }

  /* Back side */
  .card-back {
    left: 70px;
    top: 140px;
    background: var(--brand-blue);
    color: var(--card-white);
    text-align: center;
  }
  .back-mark {
    width: 70px;
    height: 70px;
    border-radius: 50%;
    background: var(--card-white);
    margin: 42px auto 12px;
  }
  .back-name {
    font-family: "Cinzel", Georgia, serif;
    font-weight: 600;
    font-size: 34px;
    letter-spacing: 2px;
    line-height: 1.1;
  }
  .back-tagline {
    font-family: "Cinzel", Georgia, serif;
    font-weight: 600;
    font-size: 11.5px;
    letter-spacing: 1.5px;
    text-transform: uppercase;
    margin-top: 10px;
    padding-top: 8px;
    border-top: 1.5px solid var(--card-white);
    display: inline-block;
  }
  .back-website {
    position: absolute;
    left: 0; right: 0;
    bottom: 30px;
    font-size: 15px;
  }

  /* Front side */
  .card-front {
    left: 610px;
    top: 460px;
    background: var(--card-white);
  }
  .front-band {
    position: absolute;
    left: 0; right: 0;
    top: 170px;
    bottom: 0;
    background: var(--brand-blue);
    border-top: 6px solid var(--card-white);
    box-shadow: 0 -3px 0 var(--brand-blue);
  }
  .front-person {
    position: absolute;
    left: 0; right: 0;
    top: 46px;
    text-align: center;
    color: var(--brand-blue);
    font-weight: 700;
    font-size: 22px;
    letter-spacing: 0.5px;
    text-transform: uppercase;
  }
  .front-mark {
    position: absolute;
    left: 190px;
    top: 100px;
    width: 140px;
    height: 140px;
    border-radius: 50%;
    background: var(--card-white);
    border: 8px solid var(--brand-blue);
    display: flex;
    align-items: center;
    justify-content: center;
    text-align: center;
  }
  .front-mark-name {
    font-family: "Cinzel", Georgia, serif;
    font-weight: 600;
    font-size: 15px;
    line-height: 1.2;
    color: var(--brand-blue);
  }
  .front-contact {
    position: absolute;
    color: var(--card-white);
    font-size: 13px;
  }
  .contact-phone { right: 30px; top: 246px; }
  .contact-lines { left: 24px; right: 24px; bottom: 14px; text-align: right; font-size: 11.5px; }
</style>
</head>
<body>
  <section class="card card-back" aria-label="Card back">
    <div class="back-mark"></div>
    <div class="back-name">Harborline Renewal</div>
    <div class="back-tagline">Specializing in Water Damage Restoration</div>
    <div class="back-website">www.HarborlineRenewal.example</div>
  </section>

  <section class="card card-front" aria-label="Card front">
    <div class="front-band"></div>
    <div class="front-person">Darnell Quisby</div>
    <div class="front-mark"><span class="front-mark-name">Harborline<br>Renewal</span></div>
    <div class="front-contact contact-phone">P: 555-318-2046</div>
    <div class="front-contact contact-lines">E: Darnell@HarborlineRenewal.example&nbsp; W: www.HarborlineRenewal.example</div>
  </section>
</body>
</html>
```